(2) Graphics for Online Store. Creative Minds Welcome+

Need (2) Different Graphics for an Online Store selling digital goods.

The digital goods are 'Leads' for Business Loan Brokers. The graphic should resemble 'Money' in some creative way.

#1 Aged Business Funding Leads
# 2 'Business Funding Real Time Calls

Preferred Colors: White/Black/Aqua

Examples of each included below. Not looking for replicas. The attached are examples of similar products only. No Clipart Please! Needs to be a Professional Clean Look! Do not replicate or emulate the attached. This is just an example.

```html
<!DOCTYPE html>
<html lang="en">
<head>
<meta charset="utf-8">
<title>Business Funding Real Time Calls</title>
<link rel="stylesheet" href="https://fonts.googleapis.com/css2?family=Montserrat:wght@800;900&display=swap">
<style>
  :root {
    --ink-deep: #07101a;
    --ink-navy: #0e2236;
    --steel: #2d4a66;
    --steel-light: #4a6f94;
    --aqua: #5ab8f2;
    --aqua-dark: #2f7fc0;
    --white: #ffffff;
    --scene-grey: #7f8f9c;
    --scene-slate: #4d5f70;
    --bill-green: #b9c7a6;
    --bill-cream: #dfe2cf;
    --suit-navy: #1e3550;
  }
  html, body {
    margin: 0;
    padding: 0;
    width: 1200px;
    height: 667px;
    overflow: hidden;
    background: var(--ink-deep);
  }
  .banner {
    position: relative;
    width: 1200px;
    height: 667px;
    overflow: hidden;
    background: linear-gradient(100deg, var(--ink-navy) 0%, #122a40 45%, var(--ink-deep) 100%);
    font-family: "Montserrat", "Arial Black", sans-serif;
  }
  .banner__stripes {
    position: absolute;
    inset: 0;
  }
  .banner__photo {
    position: absolute;
    left: 0;
    top: 0;
    width: 760px;
    height: 667px;
    background:
      radial-gradient(ellipse 180px 120px at 110px 90px, rgba(223, 226, 207, 0.75), rgba(223, 226, 207, 0) 100%),
      radial-gradient(ellipse 160px 110px at 300px 60px, rgba(185, 199, 166, 0.7), rgba(185, 199, 166, 0) 100%),
      radial-gradient(ellipse 200px 140px at 90px 420px, rgba(185, 199, 166, 0.65), rgba(185, 199, 166, 0) 100%),
      radial-gradient(ellipse 150px 110px at 240px 260px, rgba(223, 226, 207, 0.6), rgba(223, 226, 207, 0) 100%),
      radial-gradient(ellipse 260px 170px at 180px 620px, rgba(30, 53, 80, 0.9), rgba(30, 53, 80, 0) 100%),
      radial-gradient(ellipse 150px 220px at 370px 330px, rgba(205, 170, 150, 0.45), rgba(205, 170, 150, 0) 100%),
      linear-gradient(90deg, var(--scene-grey) 0%, var(--scene-slate) 55%, rgba(30, 52, 74, 0) 100%);
    -webkit-mask-image: linear-gradient(90deg, #000 58%, transparent 100%);
    mask-image: linear-gradient(90deg, #000 58%, transparent 100%);
  }
  .headline {
    margin: 0;
    position: absolute;
    right: 85px;
    top: 40px;
    text-align: right;
    font-weight: 900;
    font-size: 120px;
    line-height: 133px;
    letter-spacing: -1px;
    text-transform: uppercase;
  }
  .headline__line {
    display: block;
  }
  .headline__line--aqua { color: var(--aqua); }
  .headline__line--white { color: var(--white); }
  .chevrons {
    position: absolute;
    left: 442px;
    top: 474px;
  }
</style>
</head>
<body>
  <main class="banner">
    <svg class="banner__stripes" width="1200" height="667" viewBox="0 0 1200 667" aria-hidden="true">
      <polygon points="1010,0 1200,0 1200,90 890,667 700,667" fill="var(--steel)" opacity="0.35"/>
      <polygon points="1120,0 1200,0 1200,40 860,667 780,667" fill="var(--steel-light)" opacity="0.35"/>
      <polygon points="1200,200 1200,330 1020,667 900,667" fill="var(--aqua-dark)" opacity="0.45"/>
      <polygon points="1200,420 1200,520 1120,667 1060,667" fill="var(--aqua)" opacity="0.35"/>
    </svg>

    <div class="banner__photo" role="img" aria-label="Photo: a businessman in a navy suit taps a smartphone with his finger while many dollar bills fly through the air around his hands"></div>

    <h1 class="headline">
      <span class="headline__line headline__line--aqua">Business</span>
      <span class="headline__line headline__line--aqua">Funding</span>
      <span class="headline__line headline__line--white">Real Time</span>
      <span class="headline__line headline__line--white">Calls</span>
    </h1>

    <svg class="chevrons" width="258" height="80" viewBox="0 0 290 90" aria-hidden="true">
      <polygon points="30,0 70,0 40,45 70,90 30,90 0,45" fill="#5ab8f2"/>
      <polygon points="85,0 125,0 95,45 125,90 85,90 55,45" fill="#4ea6e0"/>
      <polygon points="140,0 180,0 150,45 180,90 140,90 110,45" fill="#3f8cc6"/>
      <polygon points="195,0 235,0 205,45 235,90 195,90 165,45" fill="#3373a6"/>
      <polygon points="250,0 290,0 260,45 290,90 250,90 220,45" fill="#2a5e88"/>
    </svg>
  </main>
</body>
</html>
```